Letter and Envelope Design For Harborline Realty

Please design a letter and an envelope incorporating our logo (See Attached). We are also launched a business card contest. Since we want them to match, please feel free to submit a design for both the business card and also the letter design and envelope.

Requirements
Must have
• The envelope, the letter and the business cards must match somehow connecting the designs. We want them to have something that holds them together besides the logo.

```html
<!DOCTYPE html>
<html lang="en">
<head>
<meta charset="utf-8">
<title>Harborline Realty – Letterhead and Envelope</title>
<link href="https://fonts.googleapis.com/css2?family=Source+Sans+3:wght@400;600&family=Arimo:wght@700&display=swap" rel="stylesheet">
<style>
  :root {
    --backdrop: #e4e4e4;
    --paper: #fafafa;
    --navy: #1c1f8f;
    --ink: #4a4a4a;
    --ink-soft: #5c5c5c;
    --rule: #c9c9c9;
    --shadow: rgba(0,0,0,0.18);
  }
  * { margin: 0; padding: 0; box-sizing: border-box; }
  html, body { width: 1200px; height: 825px; overflow: hidden; }
  body {
    background: var(--backdrop);
    position: relative;
    font-family: "Source Sans 3", sans-serif;
    color: var(--ink);
  }
  .sheet {
    position: absolute;
    background: var(--paper);
    box-shadow: 0 2px 6px var(--shadow);
  }
  .letterhead { left: 80px; top: 85px; width: 462px; height: 654px; }
  .envelope-front { left: 580px; top: 251px; width: 532px; height: 231px; }
  .envelope-back { left: 580px; top: 508px; width: 536px; height: 231px; }

  .brand {
    position: absolute;
    width: 130px;
    display: flex;
    flex-direction: column;
    align-items: center;
    gap: 6px;
  }
  .brand-dot {
    width: 46px; height: 46px;
    border: 3px solid var(--navy);
    border-radius: 50%;
  }
  .brand-name {
    font-weight: 600;
    font-size: 14px;
    letter-spacing: 1.5px;
    text-transform: uppercase;
    color: var(--navy);
    text-align: center;
    line-height: 1.15;
  }
  .letterhead .brand { left: 41px; top: 22px; }
  .envelope-front .brand { left: 39px; top: 16px; }

  .contact {
    position: absolute;
    font-size: 6.6px;
    line-height: 10px;
    color: var(--ink);
    border-left: 1px solid var(--ink-soft);
    padding-left: 3px;
  }
  .letterhead .contact { left: 337px; top: 40px; }
  .envelope-front .contact { left: 403px; top: 31px; }
  .contact-address { margin-bottom: 3px; }
  .contact-line { display: flex; align-items: center; gap: 4px; }
  .contact-line svg { width: 7px; height: 7px; flex: none; }

  .salutation {
    position: absolute;
    left: 42px; top: 136px;
    font-family: "Arimo", sans-serif;
    font-weight: 700;
    font-size: 10.5px;
    color: #222;
  }
  .letter-body {
    position: absolute;
    left: 42px; top: 162px;
    width: 380px;
    font-size: 9.6px;
    line-height: 12.1px;
    text-align: justify;
    color: var(--ink-soft);
  }
  .letter-body p { margin-bottom: 12px; }
  .signature {
    position: absolute;
    left: 42px; top: 478px;
    width: 74px; height: 34px;
    background: linear-gradient(90deg, #e6e6e6, #efefef);
    border-radius: 3px;
  }

  .address-window {
    position: absolute;
    left: 38px; top: 140px;
    width: 205px; height: 61px;
    border: 1px solid #e2e2e2;
    border-radius: 5px;
    padding: 15px 8px 0;
  }
  .address-window span {
    display: block;
    height: 11px;
    border-bottom: 1px dotted #b5b5b5;
  }
  .envelope-flap { position: absolute; left: 0; top: 0; width: 536px; height: 60px; }
</style>
</head>
<body>

<section class="sheet letterhead">
  <div class="brand">
    <div class="brand-dot"></div>
    <div class="brand-name">Harborline<br>Realty</div>
  </div>
  <address class="contact">
    <div class="contact-address">Po. box 201, Street Name,<br>City Name, Zip Code - 00000</div>
    <div class="contact-line"><svg viewBox="0 0 8 8"><rect width="8" height="8" rx="1" fill="#1c1f8f"/><path d="M2.2 2c.3 1.8 1.6 3.2 3.6 3.8l.3-.9-1-.4-.5.4c-.6-.4-1-.9-1.3-1.5l.4-.5-.4-1z" fill="#fff"/></svg>555-014-2290</div>
    <div class="contact-line"><svg viewBox="0 0 8 8"><rect width="8" height="8" rx="1" fill="#1c1f8f"/><rect x="1.6" y="2.4" width="4.8" height="3.2" fill="none" stroke="#fff" stroke-width=".7"/><path d="M1.6 2.4 4 4.3l2.4-1.9" fill="none" stroke="#fff" stroke-width=".6"/></svg>info@harborline.com</div>
    <div class="contact-line"><svg viewBox="0 0 8 8"><rect width="8" height="8" rx="1" fill="#1c1f8f"/><circle cx="4" cy="4" r="2.3" fill="none" stroke="#fff" stroke-width=".6"/><path d="M1.7 4h4.6M4 1.7v4.6" stroke="#fff" stroke-width=".5"/></svg>www.harborline.com</div>
  </address>

  <p class="salutation">Dear Mr. John,</p>
  <div class="letter-body">
    <p>Lorem Ipsum is simply dummy text of the printing and typesetting industry. Lorem Ipsum has been the industry's standard dummy text ever since the 1500s, when an unknown printer took a galley of type and scrambled it to make a type specimen book. It has survived not only five centuries, but also the leap into electronic typesetting, remaining essentially unchanged.</p>
    <p>The standard chunk of Lorem Ipsum used since the 1500s is reproduced below for those interested. Sections 1.10.32 and 1.10.33 from "de Finibus Bonorum et Malorum" by Cicero are also reproduced in their exact original form, accompanied by English versions from the 1914 translation by H. Rackham</p>
    <p>Lorem Ipsum is simply dummy text of the printing and typesetting industry. Lorem Ipsum has been the industry's standard dummy text ever since the 1500s, when an unknown printer took a galley of type and scrambled it to make a type specimen book. It has survived not only five centuries, but also the leap into electronic typesetting, remaining essentially unchanged. It was popularised in the</p>
    <p>The standard chunk of Lorem Ipsum used since the 1500s is reproduced below for those interested. Sections 1.10.32 and 1.10.33 from "de Finibus Bonorum et Malorum" by Cicero are also reproduced in their exact original form, accompanied by English versions from the 1914 translation by H. Rackham</p>
    <p>The standard chunk of Lorem Ipsum used since the 1500s is reproduced below for those interested. Sections 1.10.32 and 1.10.33 from "de Finibus Bonorum et Malorum" by Cicero are</p>
  </div>
  <div class="signature" role="img" aria-label="Handwritten signature of the sender"></div>
</section>

<section class="sheet envelope-front">
  <div class="brand">
    <div class="brand-dot"></div>
    <div class="brand-name">Harborline<br>Realty</div>
  </div>
  <address class="contact">
    <div class="contact-address">Po. box 201, Street Name,<br>City Name, Zip Code - 00000</div>
    <div class="contact-line"><svg viewBox="0 0 8 8"><rect width="8" height="8" rx="1" fill="#1c1f8f"/><path d="M2.2 2c.3 1.8 1.6 3.2 3.6 3.8l.3-.9-1-.4-.5.4c-.6-.4-1-.9-1.3-1.5l.4-.5-.4-1z" fill="#fff"/></svg>555-014-2290</div>
    <div class="contact-line"><svg viewBox="0 0 8 8"><rect width="8" height="8" rx="1" fill="#1c1f8f"/><rect x="1.6" y="2.4" width="4.8" height="3.2" fill="none" stroke="#fff" stroke-width=".7"/><path d="M1.6 2.4 4 4.3l2.4-1.9" fill="none" stroke="#fff" stroke-width=".6"/></svg>info@harborline.com</div>
    <div class="contact-line"><svg viewBox="0 0 8 8"><rect width="8" height="8" rx="1" fill="#1c1f8f"/><circle cx="4" cy="4" r="2.3" fill="none" stroke="#fff" stroke-width=".6"/><path d="M1.7 4h4.6M4 1.7v4.6" stroke="#fff" stroke-width=".5"/></svg>www.harborline.com</div>
  </address>
  <div class="address-window"><span></span><span></span><span></span></div>
</section>

<section class="sheet envelope-back">
  <svg class="envelope-flap" viewBox="0 0 536 60">
    <path d="M4 0V38Q4 57 26 57H510Q532 57 532 38V0" fill="none" stroke="#e0e0e0" stroke-width="1.2"/>
  </svg>
</section>

</body>
</html>
```